BOLD & MINIMALIST DESIGN NEEDED

We want a very bold but minimalistic business card design that is impactful and utilizes both sides of the business card. Our current logo is included for your use.

We want bold fonts and good use of negative space. We don't want the logo to overpower the design.

Target Market(s)

Professionals who are building new commercial buildings.

Industry/Entity Type

Construction

Contact Information for Business Card

Name, Title, email, office phone, cell phone, website

Font styles to use
Serif
Sans Serif

Requirements
Must have
• Bold design!

```html
<!DOCTYPE html>
<html lang="en">
<head>
<meta charset="utf-8">
<title>Summitline Business Card</title>
<link rel="stylesheet" href="https://fonts.googleapis.com/css2?family=Montserrat:wght@400;500;600;800&display=swap">
<style>
  :root {
    --backdrop: #2b2b2b;
    --card: #222223;
    --white: #f2f2f2;
    --muted: #d6d6d6;
    --green: #76b22b;
    --ink: #1d1d1d;
    --steel-dark: #1b1b1b;
    --steel-light: #6e6e6e;
    --paper: #e9e9e9;
  }
  * { margin: 0; padding: 0; box-sizing: border-box; }
  html, body {
    width: 1200px; height: 576px; overflow: hidden;
    background: var(--backdrop);
    font-family: "Montserrat", sans-serif;
  }
  .stage { position: relative; width: 1200px; height: 576px; }
  .card {
    position: absolute; top: 139px; width: 484px; height: 293px;
    background: var(--card);
    border-radius: 8px;
    box-shadow: 0 4px 10px rgba(0,0,0,.45);
    overflow: hidden;
  }
  .card--front { left: 102px; }
  .card--back { left: 596px; }

  .brand-name {
    position: absolute;
    font-family: "Montserrat", sans-serif;
    font-weight: 800;
    font-size: 32px;
    line-height: 1;
    color: var(--white);
    letter-spacing: 1px;
    white-space: nowrap;
  }
  .card--front .brand-name { left: 48px; top: 128px; }
  .card--back .brand-name { left: 26px; top: 36px; }

  .emblem-area { position: absolute; }
  .card--front .emblem-area {
    left: 320px; top: 0; width: 164px; height: 293px;
    background: linear-gradient(90deg, var(--steel-dark) 0%, #3a3a3a 45%, var(--steel-light) 100%);
  }
  .card--back .emblem-area {
    left: 296px; top: 37px; width: 188px; height: 256px;
    background: linear-gradient(90deg, var(--paper) 0%, #d9e8c6 50%, var(--green) 100%);
  }

  .name-band {
    position: absolute; left: 0; top: 125px;
    width: 284px; height: 67px;
    background: var(--green);
    padding: 14px 0 0 25px;
  }
  .person-name {
    font-size: 20px; font-weight: 600; color: var(--ink); line-height: 1.1;
  }
  .person-title {
    font-size: 11px; font-weight: 500; color: var(--ink); margin-top: 5px;
  }

  .contact-list {
    position: absolute; left: 25px; top: 219px;
    list-style: none;
  }
  .contact-list li {
    display: flex; align-items: center;
    height: 17px;
    font-size: 12px; color: var(--muted);
  }
  .contact-list svg { width: 11px; height: 11px; margin-right: 8px; flex: none; }
</style>
</head>
<body>
<main class="stage">
  <section class="card card--front" aria-label="Card front">
    <div class="brand-name">SUMMITLINE</div>
    <div class="emblem-area" role="img" aria-label="Large brand emblem in brushed steel"></div>
  </section>

  <section class="card card--back" aria-label="Card back">
    <div class="brand-name">SUMMITLINE</div>
    <div class="emblem-area" role="img" aria-label="Large brand emblem in white and green"></div>

    <div class="name-band">
      <div class="person-name">Daniel Reyes</div>
      <div class="person-title">Director</div>
    </div>

    <ul class="contact-list">
      <li>
        <svg viewBox="0 0 12 12" aria-hidden="true"><path fill="var(--green)" d="M1 4c0-2 2-3 5-3s5 1 5 3l-2 1-1-1.5H4L3 5zM3 6h6l1 5H2z"/></svg>
        555-014-2290
      </li>
      <li>
        <svg viewBox="0 0 12 12" aria-hidden="true"><rect x="0.5" y="2.5" width="11" height="7" fill="var(--green)"/><path d="M0.5 2.5 6 7l5.5-4.5" fill="none" stroke="var(--card)" stroke-width="1"/></svg>
        daniel@summitline.com
      </li>
      <li>
        <svg viewBox="0 0 12 12" aria-hidden="true"><circle cx="6" cy="6" r="5" fill="var(--green)"/><path d="M1 6h10M6 1c-2.5 3-2.5 7 0 10M6 1c2.5 3 2.5 7 0 10" fill="none" stroke="var(--card)" stroke-width=".8"/></svg>
        www.summitline.com
      </li>
    </ul>
  </section>
</main>
</body>
</html>
```